Hearthside Lending Relief

Please help us give our website a remake or a FACELIFT. It is not very good but it says what we need it to say. But the design is terrible.
I would like our new design font and logo to be used as the theme.

I also want more photos on the site.

I also want consistency with the pages so they look clean.

We want the professionals to do this, let's see what you got!

Thank you!
Updates

Project Deadline Extended
Reason: I can understand you want to be paid. So I will commit to the fee but I want you to have time to make a KICK ASS website for me dudes! Thanks

HI!  Just wanted to say thanks for your time on these.  A lot are great.  However the firefighters have nothing to do with Foreclosure.  We are saving peoples homes from the bank taking them and selling them.   I LOVE the house photos and the families on the website.  That is the direction we like.  THanks.

THANK U ALL FOR THE WORK!   I like a few ending in the numbers: 147  733  693  536  620  478  727  508     I will go over them and choose one soon.  Thank you.   You will be paid shortly. 

Requirements
Must have
• Bright, Upbeat photos. Color scheme should be in order. We like icons on the bottom. not just text.

```html
<!DOCTYPE html>
<html lang="en">
<head>
<meta charset="utf-8">
<title>Hearthside Lending Relief – Who We Are</title>
<link rel="stylesheet" href="https://fonts.googleapis.com/css2?family=Noto+Sans:wght@400;700&display=swap">
<style>
:root{
  --red:#d7191f;
  --black:#000;
  --ink:#111;
  --text:#555;
  --muted:#6a6a6a;
  --panel:#dcdcdc;
  --field:#d6d6d6;
  --white:#fff;
}
*{box-sizing:border-box;margin:0;padding:0}
html,body{width:1200px;height:857px;overflow:hidden;background:var(--white)}
body{position:relative;font-family:"Noto Sans",Arial,sans-serif;color:var(--text)}
.brand{position:absolute;left:108px;top:25px;display:flex;align-items:center;gap:16px}
.brand-dot{width:100px;height:100px;border-radius:50%;background:var(--red)}
.brand-name{font-weight:700;font-size:25px;line-height:30px;color:var(--ink);text-transform:uppercase;width:240px}
.callout{position:absolute;left:846px;top:50px;display:flex;gap:12px}
.callout-number{font-size:28px;line-height:34px;color:var(--muted);letter-spacing:.5px}
.callout-label{font-size:20px;line-height:26px;color:var(--red);margin-left:-2px}
.main-nav{position:absolute;left:0;top:153px;width:1200px;height:27px;background:var(--black)}
.main-nav a{position:absolute;top:0;height:27px;line-height:28px;color:var(--white);font-size:13px;text-decoration:none;text-align:center}
.nav-gap{position:absolute;top:0;width:4px;height:27px;background:var(--white)}
.search-field{position:absolute;left:960px;top:4px;width:150px;height:19px;background:var(--field)}
.search-icon{position:absolute;left:933px;top:3px}
.about{position:absolute;left:86px;top:194px;width:712px}
.about h1{color:var(--red);font-size:20px;font-weight:700;line-height:24px}
.team{position:relative;height:261px;margin-top:2px}
.member{position:absolute;top:0}
.member-photo{height:212px}
.member-caption{font-size:13px;line-height:16px;color:var(--text);margin-top:4px;padding-left:3px}
.about p{font-size:13px;line-height:16.5px;text-align:justify;margin-bottom:16px}
.testimonials{position:absolute;left:815px;top:184px;width:296px;height:584px;background:var(--panel)}
.testimonials h2{height:35px;background:var(--red);color:var(--white);font-size:19px;font-weight:700;display:flex;align-items:center;gap:10px;padding-left:16px}
.quote{padding:0 19px 0 18px;font-size:13.5px;line-height:14.9px;color:var(--muted);text-align:justify;hyphens:auto;letter-spacing:.25px}
.quote-author{text-align:right;margin-top:1px;margin-bottom:16px}
.site-footer{position:absolute;left:86px;top:775px;width:1027px;height:33px;background:var(--black);color:var(--white);font-size:13px;line-height:34px;padding-left:14px}
.legal{position:absolute;top:819px;font-size:13px;color:var(--text)}
</style>
</head>
<body>
<header>
  <div class="brand">
    <span class="brand-dot"></span>
    <span class="brand-name">Hearthside Lending Relief</span>
  </div>
  <div class="callout">
    <svg width="46" height="46" viewBox="0 0 46 46" aria-hidden="true">
      <circle cx="23" cy="23" r="21" fill="none" stroke="#6a6a6a" stroke-width="3"/>
      <path d="M16 11c2-1 3 0 4 2l2 4c1 2 0 3-1 4l-1 1c1 3 3 5 6 7l1-1c1-1 2-2 4-1l4 2c2 1 3 2 2 4l-1 2c-1 2-3 3-6 2-7-3-13-9-15-16-1-4 0-8 1-10z" fill="#6a6a6a"/>
    </svg>
    <div>
      <div class="callout-number">877.555.0148</div>
      <div class="callout-label">Call Tall Free Now</div>
    </div>
  </div>
</header>

<nav class="main-nav">
  <a href="#" style="left:80px;width:110px">HOME</a>
  <span class="nav-gap" style="left:195px"></span>
  <a href="#" style="left:199px;width:153px">WHO WE ARE</a>
  <span class="nav-gap" style="left:352px"></span>
  <a href="#" style="left:356px;width:125px">SERVICES</a>
  <span class="nav-gap" style="left:480px"></span>
  <a href="#" style="left:484px;width:193px">FINANCING OPTIONS</a>
  <span class="nav-gap" style="left:676px"></span>
  <a href="#" style="left:680px;width:131px">CONTACT US</a>
  <span class="nav-gap" style="left:811px"></span>
  <a href="#" style="left:815px;width:106px">SPANISH</a>
  <svg class="search-icon" width="22" height="22" viewBox="0 0 22 22" aria-hidden="true">
    <circle cx="9" cy="9" r="6.5" fill="none" stroke="#fff" stroke-width="2.5"/>
    <path d="M14 14l6 6" stroke="#fff" stroke-width="3" stroke-linecap="round"/>
  </svg>
  <span class="search-field"></span>
</nav>

<main class="about">
  <h1>WHO WE ARE</h1>
  <div class="team">
    <div class="member" style="left:0;width:172px">
      <div class="member-photo" role="img" aria-label="Bright portrait of a smiling team member in a white shirt and striped tie holding papers at a desk" style="background:radial-gradient(ellipse at 50% 75%,#ffffff 0%,#f1f1f1 40%,#b8b8b8 85%,#6e6e6e 100%)"></div>
      <div class="member-caption">Team Memeber Name<br>Title</div>
    </div>
    <div class="member" style="left:176px;width:175px">
      <div class="member-photo" role="img" aria-label="Bright portrait of a team member in a navy suit and blue tie in a leafy, sunlit office" style="background:linear-gradient(165deg,#d9e8b0 0%,#93b560 30%,#4d6a8f 60%,#24305a 100%)"></div>
      <div class="member-caption">Team Memeber Name<br>Title</div>
    </div>
    <div class="member" style="left:355px;width:175px">
      <div class="member-photo" role="img" aria-label="Bright portrait of a team member in a dark blazer working at a computer in a white office" style="background:linear-gradient(180deg,#fafcfd 0%,#e3eaf0 40%,#4a5366 75%,#e8ecef 100%)"></div>
      <div class="member-caption">Team Memeber Name<br>Title</div>
    </div>
    <div class="member" style="left:535px;width:175px">
      <div class="member-photo" role="img" aria-label="Bright portrait of a senior team member with glasses and a light blue shirt at a laptop" style="background:linear-gradient(180deg,#f0f0f0 0%,#c9d3e2 45%,#9fb2cc 75%,#7d8a9c 100%)"></div>
      <div class="member-caption">Team Memeber Name<br>Title</div>
    </div>
  </div>
  <p>HEARTHSIDE LENDING RELIEF specializes in assisting home owners who are in the foreclosure process. We understand that there are many reasons why homeowners are unable to pay their mortgages and that every situation is in fact unique.</p>
  <p>HEARTHSIDE LENDING RELIEF takes the time to meet with homeowners and explain the options you have to the foreclosure process. We have found that in most cases the foreclosure can be prevented. Our specialist will meet with you personally to help assess the situation and offer you other options to foreclosure.</p>
  <p>We have the ability, knowledge and capitol necessary to take decisive action to help stop your home from being foreclosed. We are located in Downtown San Diego, CA across the street from the court house.</p>
  <p>HEARTHSIDE LENDING RELIEF covers the entire Southern California Area, from Ventura to the Mexican boarder.</p>
  <p>Our skill and integrity has earned us a reputation for the "#1 provider of foreclosure solutions in all of Southern California".</p>
  <p>HEARTHSIDE LENDING RELIEF has over 50 years of real estate knowledge and experience.</p>
</main>

<aside class="testimonials">
  <h2>
    <svg width="30" height="28" viewBox="0 0 30 28" aria-hidden="true">
      <path d="M3 3h24v17H12l-6 6v-6H3z" fill="none" stroke="#fff" stroke-width="3" stroke-linejoin="round"/>
    </svg>
    TESTIMONIALS
  </h2>
  <div class="quote" style="margin-top:13px">
    <p>“Dear Theo,<br>I'd like to express my gratitude to you and your company and I have to add, for all of the trustworthy and reliable service that you bring to the public. Your company helped put me back together, you in particular are awesome! Thank you again Theo.”</p>
    <p class="quote-author">- Rosalind</p>
    <p>“Hearthside Lending Relief has been an absolute life saver for me and my family. Their services have changed everything. Instead of my house going into foreclosure and losing everything I own, I now have a chance to start over and the money to do it with! They've been fast, friendly and efficient. I would recommend their services to anyone facing foreclosure.”</p>
    <p class="quote-author" style="margin-top:14px">- Dana W.</p>
    <p>“I owe you guys a big thank you. The stress of this whole thing was almost too much for me. I didn't believe that you could help at first to be honest. You have done everything you said you would and you were very considerate of us. We are pleased to have been able to dictate our own choices in this and to walk away with more money than we expected.Thanks again guys.”</p>
    <p class="quote-author">- Gerald M.</p>
  </div>
</aside>

<footer>
  <div class="site-footer">Home I Who We Are I Services I Financial Options I Contact Us</div>
  <div class="legal" style="left:98px">© 2012 HEARTHSIDELENDINGRELIEF.COM. All rights reserved.</div>
  <div class="legal" style="right:105px">1180 Larkspur Avenue, Suite 300, San Diego, CA 92101, 877.555.0148</div>
</footer>
</body>
</html>
```